New Innovative Counselling and psychotherapy Service needs Business Card design

Keep it simple and professional. On one side, just company name and logo (perhaps in all blue) and maybe a tag line.

On other side (all white) my name and Qualifications in centre

Industry/Entity Type

Health And Wellness

Contact Information for Business Card

Dara Whelby
Counsellor & Psychotherapist
BSc (Psychol.), BA, Dip. (Couns. & Psych.), PG.Cert (CBT), FGTrK, ONRE

I will also require Mobile no, Email and web site address of which I'll pass on to final designer.

Font styles to use
Sans Serif

Requirements
Must have
• My Logo Only and please use the colours in logo that is in it.
Should not have
• Any other images

```html
<!DOCTYPE html>
<html lang="en">
<head>
<meta charset="utf-8">
<title>Thrive Harbour – Business Card</title>
<link href="https://fonts.googleapis.com/css2?family=Roboto:wght@400;500;700&display=swap" rel="stylesheet">
<style>
  :root {
    --backdrop: #3a3a3c;
    --card: #1f1f21;
    --card-edge: #141415;
    --blue: #3fa9e8;
    --green: #8cc63f;
    --text-light: #e8e8ea;
    --emboss: #4a4a4e;
  }
  * { margin: 0; padding: 0; box-sizing: border-box; }
  html, body {
    width: 799px; height: 1200px; overflow: hidden;
    background: var(--backdrop);
    font-family: 'Roboto', Arial, sans-serif;
  }
  .sheet { position: relative; width: 799px; height: 1200px; }
  .card {
    position: absolute; left: 80px; width: 640px; height: 370px;
    background: var(--card); border-radius: 22px; overflow: hidden;
    box-shadow: 0 6px 0 var(--card-edge), 0 18px 40px rgba(0,0,0,.45);
  }
  .card--front { top: 130px; }
  .card--back { top: 690px; }

  /* Front */
  .front-mark {
    position: absolute; inset: 0;
    display: flex; align-items: center; justify-content: center; gap: 18px;
  }
  .front-mark__dot {
    width: 58px; height: 58px; border-radius: 50%; background: var(--emboss);
  }
  .front-mark__name {
    font-size: 40px; font-weight: 500; color: var(--emboss); letter-spacing: .5px;
  }

  /* Back */
  .corner-arc { position: absolute; left: 0; top: 0; }
  .person { position: absolute; left: 48px; top: 38px; }
  .person__name { font-size: 24px; font-weight: 700; color: var(--blue); margin-bottom: 8px; }
  .person__role, .person__quals {
    font-size: 14px; line-height: 17px; color: var(--text-light);
  }
  .contact { position: absolute; left: 48px; top: 198px; list-style: none; }
  .contact__item {
    display: flex; align-items: center; gap: 14px;
    font-size: 15px; line-height: 22px; color: var(--text-light);
  }
  .contact__icon { width: 13px; height: 13px; flex: none; }
  .brand {
    position: absolute; right: 46px; bottom: 52px;
    display: flex; align-items: center; gap: 12px;
  }
  .brand__dot { width: 26px; height: 26px; border-radius: 50%; background: var(--blue); }
  .brand__name { font-size: 28px; font-weight: 400; color: #ffffff; }
  .edge-band { position: absolute; left: 0; bottom: 0; width: 100%; height: 9px; display: flex; }
  .edge-band__blue { width: 48%; background: var(--blue); }
  .edge-band__green { flex: 1; background: var(--green); }
</style>
</head>
<body>
<main class="sheet">

  <section class="card card--front" aria-label="Card front">
    <div class="front-mark">
      <span class="front-mark__dot"></span>
      <span class="front-mark__name">Thrive Harbour</span>
    </div>
  </section>

  <section class="card card--back" aria-label="Card back">
    <svg class="corner-arc" width="40" height="90" viewBox="0 0 40 90">
      <defs>
        <linearGradient id="arcFill" x1="0" y1="0" x2="0" y2="1">
          <stop offset="0" stop-color="#3fa9e8"/>
          <stop offset="1" stop-color="#8cc63f"/>
        </linearGradient>
      </defs>
      <path d="M0 0 H22 Q36 40 0 86 Z" fill="url(#arcFill)"/>
    </svg>

    <div class="person">
      <h1 class="person__name">Dara Whelby</h1>
      <p class="person__role">Counsellor &amp; Psychotherapist</p>
      <p class="person__quals">BSc (Psychol.), BA, Dip. (Couns. &amp; Psych.)<br>PG.Cert (CBT), FGTrK, ONRE</p>
    </div>

    <ul class="contact">
      <li class="contact__item">
        <svg class="contact__icon" viewBox="0 0 14 14"><path d="M3 1 L5 1 L6 4 L4.5 5.5 Q6 8.5 8.5 9.5 L10 8 L13 9 L13 11 Q12 13 10 13 Q2 11 1 3 Q1 1 3 1 Z" fill="#8cc63f"/></svg>
        <span>4821 309 6657</span>
      </li>
      <li class="contact__item">
        <svg class="contact__icon" viewBox="0 0 14 14"><rect x="1" y="3" width="12" height="8" fill="#8cc63f"/><path d="M1 3 L7 8 L13 3" stroke="#1f1f21" stroke-width="1.2" fill="none"/></svg>
        <span>dara.w@ThriveHarbour.com</span>
      </li>
      <li class="contact__item">
        <svg class="contact__icon" viewBox="0 0 14 14"><circle cx="7" cy="7" r="6" fill="#8cc63f"/><path d="M1 7 H13 M7 1 Q3 7 7 13 Q11 7 7 1" stroke="#1f1f21" stroke-width="1" fill="none"/></svg>
        <span>www.ThriveHarbour.com</span>
      </li>
    </ul>

    <div class="brand">
      <span class="brand__dot"></span>
      <span class="brand__name">Thrive Harbour</span>
    </div>

    <div class="edge-band"><span class="edge-band__blue"></span><span class="edge-band__green"></span></div>
  </section>

</main>
</body>
</html>
```